KAJU Freightways #ALLKAJU Business Cards & Letterhead

I am looking to business cards designed for our organization. We are currently undergoing a small re-branding that is taking place. Our organization is called KAJU Freightways and we are headquartered in Phoenix, AZ. We primarily provide transportation and logistics services to the Marlow Parcel Bureau who is our largest customer. I would like to see a design that incorporates name, title, contact info, website, and address (this will be different depending on the employee). I would also like to see some color on the business card using our logo colors or a variation. I would like our logo on the back of the business card with the website displayed. The final design should communicate that we are a next generation transportation operate that focuses on being driver-first, customer-centric, innovative, and sustainable.We would also like our #ALLKAJU catch phrase incorporated as well.

Target Market(s)

Transportation & Logistics

Industry/Entity Type

Trucking Company

Contact Information for Business Card

-First and Last Name
-Position Title
-Contact Phone
-Contact Email
-Physical Address

Font styles to use
Serif

Colors

Designer to choose colors to be used in the design.

Requirements
Must have
• -KAJU logo prominently displayed
• -#ALLKAJU catch phrase used
• -Some amount of color, design gradient, etc.
• -Logo on the back with website listed (https://www.kajufreightco.example)

```html
<!DOCTYPE html>
<html lang="en">
<head>
<meta charset="utf-8">
<title>KAJU Freightways Business Cards</title>
<link href="https://fonts.googleapis.com/css2?family=Roboto+Serif:opsz,wght@8..144,400;8..144,500&family=Roboto+Slab:wght@600;700&display=swap" rel="stylesheet">
<style>
  :root {
    --navy: #0d3540;
    --green: #72ad2a;
    --paper: #f2f2f0;
    --backdrop: #bebebe;
    --ink: #1f3a44;
    --white: #ffffff;
  }
  * { margin: 0; padding: 0; box-sizing: border-box; }
  html, body { width: 1200px; height: 576px; overflow: hidden; }
  body {
    background: var(--backdrop);
    font-family: "Roboto Serif", Georgia, serif;
    position: relative;
  }
  .card {
    position: absolute;
    top: 139px;
    width: 484px;
    height: 293px;
    background: var(--paper);
    border-radius: 10px;
    overflow: hidden;
  }
  .card--back { left: 82px; }
  .card--front { left: 602px; }

  /* Back */
  .brand-mark {
    position: absolute;
    left: 0; right: 0; top: 100px;
    display: flex; justify-content: center; align-items: center; gap: 12px;
  }
  .brand-mark__dot {
    width: 22px; height: 22px; border-radius: 50%;
    background: var(--green);
  }
  .brand-mark__name {
    font-family: "Roboto Slab", Georgia, serif;
    font-weight: 700; font-size: 58px; line-height: 1;
    color: var(--navy); letter-spacing: 2px;
  }
  .back-hashtag {
    position: absolute; left: 0; right: 0; top: 176px;
    text-align: center;
    font-family: "Roboto Slab", Georgia, serif;
    font-weight: 600; font-size: 14px; letter-spacing: 3px;
    color: var(--green);
  }
  .back-web {
    position: absolute; left: 0; right: 0; top: 250px;
    display: flex; justify-content: center; align-items: center; gap: 16px;
    font-size: 12.5px; letter-spacing: 2.2px; color: var(--navy);
  }
  .back-web__dash { width: 34px; height: 2px; background: var(--green); }
  .back-band { position: absolute; left: 0; right: 0; bottom: 0; height: 13px; display: flex; }
  .back-band__navy { flex: 1; background: var(--navy); }
  .back-band__green { flex: 1; background: var(--green); }

  /* Front */
  .front-watermark {
    position: absolute; left: 300px; top: 92px;
    font-family: "Roboto Slab", Georgia, serif;
    font-weight: 700; font-size: 104px; line-height: 1;
    color: rgba(13,53,64,0.05); letter-spacing: 4px;
  }
  .front-brand {
    position: absolute; left: 24px; top: 62px;
    display: flex; align-items: center; gap: 8px;
  }
  .front-brand__dot { width: 12px; height: 12px; border-radius: 50%; background: var(--green); }
  .front-brand__name {
    font-family: "Roboto Slab", Georgia, serif;
    font-weight: 700; font-size: 30px; line-height: 1; color: var(--navy);
  }
  .front-tagline {
    position: absolute; left: 136px; top: 55px;
    font-family: "Roboto Slab", Georgia, serif;
    font-weight: 700; font-size: 21px; line-height: 25px; color: var(--navy);
  }
  .person { position: absolute; left: 24px; top: 167px; }
  .person__name {
    font-family: "Roboto Slab", Georgia, serif;
    font-weight: 700; font-size: 19px; color: var(--navy); line-height: 1.1;
  }
  .person__title {
    display: inline-block; margin-top: 5px; padding-bottom: 3px;
    font-size: 12px; color: var(--ink);
    border-bottom: 1.5px solid var(--green);
  }
  .address {
    position: absolute; left: 24px; top: 232px;
    font-style: normal;
    font-size: 12px; line-height: 18px; color: var(--ink);
  }
  .contacts {
    position: absolute; left: 268px; top: 178px;
    list-style: none; font-size: 11.5px; line-height: 18px; color: var(--ink);
  }
  .contacts li { display: flex; align-items: center; gap: 11px; }
  .contacts svg { width: 11px; height: 11px; fill: var(--green); flex: none; }
  .front-footer { position: absolute; left: 0; bottom: 0; width: 484px; height: 40px; }
  .front-footer__label {
    position: absolute; left: 236px; bottom: 13px; width: 240px;
    text-align: center; font-size: 12px; color: var(--white);
  }
</style>
</head>
<body>

<section class="card card--back" aria-label="Business card back">
  <div class="brand-mark">
    <span class="brand-mark__dot"></span>
    <span class="brand-mark__name">KAJU</span>
  </div>
  <div class="back-hashtag">#ALLKAJU</div>
  <div class="back-web">
    <span class="back-web__dash"></span>
    <span>www.kajufreightco.example</span>
    <span class="back-web__dash"></span>
  </div>
  <div class="back-band"><span class="back-band__navy"></span><span class="back-band__green"></span></div>
</section>

<section class="card card--front" aria-label="Business card front">
  <div class="front-watermark" aria-hidden="true">KAJU</div>
  <div class="front-brand">
    <span class="front-brand__name">KAJU</span>
    <span class="front-brand__dot"></span>
  </div>
  <div class="front-tagline">Transportation &amp;<br>Energy&nbsp; Services</div>

  <div class="person">
    <div class="person__name">Dorian Whitcombe</div>
    <div class="person__title">Chairman &amp; CEO</div>
  </div>
  <address class="address">4410 North Canyon Ridge<br>Drive Phoenix, AZ 85020</address>

  <ul class="contacts">
    <li><svg viewBox="0 0 12 12"><path d="M2.5 1h2l1 3-1.3 1a6 6 0 0 0 2.8 2.8L8 6.5l3 1v2A1.5 1.5 0 0 1 9.5 11 8.5 8.5 0 0 1 1 2.5 1.5 1.5 0 0 1 2.5 1z"/></svg>555-014-2290</li>
    <li><svg viewBox="0 0 12 12"><path d="M0 2h12v8H0z M0 2l6 4.5L12 2" stroke="#f2f2f0" stroke-width="1"/></svg>dorian@kajufreightco.example</li>
    <li><svg viewBox="0 0 12 12"><circle cx="6" cy="6" r="5.5"/><path d="M.5 6h11M6 .5c-3 3-3 8 0 11M6 .5c3 3 3 8 0 11" stroke="#f2f2f0" stroke-width="0.8" fill="none"/></svg>www.kajufreightco.example</li>
  </ul>

  <svg class="front-footer" viewBox="0 0 484 40" preserveAspectRatio="none" aria-hidden="true">
    <rect x="0" y="27" width="240" height="13" fill="var(--green)"/>
    <path d="M218 40 L240 4 Q242 0 248 0 L484 0 L484 40 Z" fill="var(--navy)"/>
  </svg>
  <div class="front-footer__label">KAJU Freightways &amp; Energy</div>
</section>

</body>
</html>
```